Brightway Haus Inc. Business Card Design

Brightway Haus Inc. is in search of a great clean design for our business cards!

Looking to incorporate our full logo and watermark on side one (however, I am open to having the text and watermark separated within the design.)

On side two, I am looking to have contact information (Name, Position, Phone #, Email, Website (www.thebrightwayhaus.ca). Can have the logo and/or watermark as part of the design if applicable.

Please add tagline "Where Shine Counts" on either side 1 or 2. This tagline can be in a sans serif, serif or cursive font as long as it compliments overall design. Capitalization can be title or sentence case depending on how it fits within the design.

Get creative!! Looking for a clean, crisp, premium design! Looking for a glossy card finish with spot UV features when printed. Cards will also be printed with rounded corners. Standard dimensions (3.5 x 2).

Target Market(s)

B2B - primary clients are business owners or property management corporations. (residential jobs are few and far between)

Industry/Entity Type

Business

Contact Information for Business Card

- clean, crisp design
- double sided
- spot UV accents and glossy finish upon printing
- standard business card size (3.5 x 2) with rounded corners
- please see project description for requirements per side

Font styles to use
Sans Serif

Requirements
Must have
• - adequate bleeds with print ready files
• - cohesive design elements between side 1 & 2
• - spot UV elements (can be on both sides or just one, use your discretion)
• - colour pallet should match the logo file provided
• - incorporate tagline "where shine counts" (this tagline can be in a serif or sans serif font as long as it is complimentary to the overall design.
Nice to have
• - Premium elements with a clean design
Should not have
• - Please omit cartoon or whimsical like designs, think premium.
• - Colours should not stray from the pallet of the provided logo.

```html
<!DOCTYPE html>
<html lang="en">
<head>
<meta charset="utf-8">
<title>Brightway Haus Inc. Business Card</title>
<link rel="stylesheet" href="https://fonts.googleapis.com/css2?family=Roboto:ital,wght@0,400;0,500;0,700;1,400&display=swap">
<style>
  :root {
    --backdrop: #2c2c2e;
    --navy: #1b2452;
    --teal: #12b1b3;
    --paper: #f3f3f3;
    --white: #ffffff;
    --grey: #a9a9a9;
  }
  * { margin: 0; padding: 0; box-sizing: border-box; }
  html, body { width: 1200px; height: 960px; overflow: hidden; }
  body {
    background: var(--backdrop);
    font-family: "Roboto", Arial, sans-serif;
    position: relative;
  }
  .card {
    position: absolute;
    width: 600px;
    height: 342px;
    border-radius: 22px;
    overflow: hidden;
  }
  .card--front { left: 314px; top: 114px; background: var(--navy); }
  .card--back { left: 311px; top: 472px; background: var(--paper); }

  .front-field { position: absolute; inset: 0; }

  .contact {
    position: absolute;
    right: 32px;
    top: 120px;
    text-align: right;
    color: var(--white);
  }
  .contact__name {
    color: var(--teal);
    font-size: 19px;
    font-weight: 500;
    letter-spacing: 0.2px;
    line-height: 24px;
  }
  .contact__role {
    font-size: 14px;
    font-weight: 500;
    line-height: 20px;
    margin-bottom: 12px;
  }
  .contact__address { font-size: 14px; line-height: 18px; margin-bottom: 11px; }
  .contact__list { list-style: none; }
  .contact__item {
    display: flex;
    justify-content: flex-end;
    align-items: center;
    gap: 8px;
    font-size: 14px;
    line-height: 19.5px;
  }
  .contact__icon { width: 12px; height: 12px; flex: none; }

  .brand {
    position: absolute;
    left: 0; right: 0;
    top: 146px;
    display: flex;
    justify-content: center;
    align-items: center;
    gap: 12px;
  }
  .brand__mark { width: 34px; height: 34px; background: var(--teal); }
  .brand__name {
    color: var(--navy);
    font-size: 40px;
    font-weight: 700;
    letter-spacing: -0.5px;
  }

  .tagline {
    position: absolute;
    left: 104px; right: 90px;
    top: 274px;
    display: flex;
    align-items: center;
    gap: 4px;
  }
  .tagline__rule { flex: 1; height: 1px; }
  .tagline__rule--left { background: linear-gradient(to right, transparent, var(--navy)); }
  .tagline__rule--right { background: linear-gradient(to left, transparent, var(--navy)); }
  .tagline__text {
    font-style: italic;
    font-size: 19px;
    color: var(--navy);
    white-space: nowrap;
  }
  .tagline__accent { color: var(--teal); }
</style>
</head>
<body>

<section class="card card--front" aria-label="Business card, contact side">
  <svg class="front-field" viewBox="0 0 600 342" aria-hidden="true">
    <path d="M0 0 H522 Q300 210 0 290 Z" fill="var(--teal)"/>
  </svg>
  <div class="contact">
    <p class="contact__name">MARCUS ELLERY</p>
    <p class="contact__role">CEO/FOUNDER</p>
    <p class="contact__address">2140 Harbourview Road<br>Halifax, Nova Scotia 38215</p>
    <ul class="contact__list">
      <li class="contact__item">902 555 0184
        <svg class="contact__icon" viewBox="0 0 12 12"><path d="M2.5 0.8 L4.6 3 L3.5 4.4 Q4.6 6.8 7.6 8.5 L9 7.4 L11.2 9.5 L9.8 11.2 Q5.5 11 2.2 6.8 Q0.6 4.2 0.8 2.3 Z" fill="var(--teal)"/></svg>
      </li>
      <li class="contact__item">902 555 0127
        <svg class="contact__icon" viewBox="0 0 12 12"><rect x="3" y="0.5" width="6.5" height="11" rx="1.2" fill="none" stroke="var(--teal)" stroke-width="1.2"/><circle cx="6.25" cy="9.6" r="0.7" fill="var(--teal)"/></svg>
      </li>
      <li class="contact__item">902 555 0163
        <svg class="contact__icon" viewBox="0 0 12 12"><rect x="3" y="1" width="6" height="3" fill="var(--teal)"/><rect x="0.5" y="4.5" width="11" height="5" rx="1" fill="var(--teal)"/><rect x="3" y="8" width="6" height="3" fill="var(--white)" stroke="var(--teal)" stroke-width="0.8"/></svg>
      </li>
      <li class="contact__item">marcus@thebrightwayhaus.ca
        <svg class="contact__icon" viewBox="0 0 12 12"><rect x="0.5" y="2.5" width="11" height="7.5" fill="var(--teal)"/><path d="M0.8 2.8 L6 7 L11.2 2.8" fill="none" stroke="var(--navy)" stroke-width="1"/></svg>
      </li>
      <li class="contact__item">www.thebrightwayhaus.ca
        <svg class="contact__icon" viewBox="0 0 12 12"><circle cx="6" cy="6" r="5.4" fill="var(--teal)"/><path d="M6 0.6 V11.4 M0.6 6 H11.4 M6 0.6 Q2.8 6 6 11.4 M6 0.6 Q9.2 6 6 11.4" fill="none" stroke="var(--navy)" stroke-width="0.7"/></svg>
      </li>
    </ul>
  </div>
</section>

<section class="card card--back" aria-label="Business card, brand side">
  <div class="brand">
    <span class="brand__mark"></span>
    <span class="brand__name">Brightway Haus Inc.</span>
  </div>
  <div class="tagline">
    <span class="tagline__rule tagline__rule--left"></span>
    <span class="tagline__text">Where <span class="tagline__accent">Shine</span> Counts</span>
    <span class="tagline__rule tagline__rule--right"></span>
  </div>
</section>

</body>
</html>
```